Marlowe Group needs a business card

I would like the card to be simple but modern and elegant.
I like black and white.
or black and gold.
we are a private finance lender and also are involved in property and property developments.

please look at the business card photos i provided i would like M.G only one one side and all the other details on the other side use fonts that tie in with my theme.

Industry/Entity Type

Finance

Contact Information for Business Card

Marlowe Group (M.G) Daniel Marlowe M: 0413586207 E: danmarl@inboxmail.test

Font styles to use
Other font styles liked:
• Use fonts that would reflect our business

Colors
000000
ffffff

Requirements
Must have
• one side of details
• other side has either M.G or Marlowe Group like in the photos provided

```html
<!DOCTYPE html>
<html lang="en">
<head>
<meta charset="utf-8">
<title>Marlowe Group — Business Card</title>
<link rel="stylesheet" href="https://fonts.googleapis.com/css2?family=Open+Sans:wght@400;600;800&display=swap">
<style>
  :root {
    --ink: #000000;
    --paper: #ffffff;
    --backdrop: #e9e9e7;
    --faint-mark: #d9d9d9;
    --shadow: rgba(0, 0, 0, 0.18);
  }
  * { margin: 0; padding: 0; box-sizing: border-box; }
  html, body {
    width: 1200px;
    height: 987px;
    overflow: hidden;
  }
  body {
    position: relative;
    background: var(--backdrop);
    font-family: "Open Sans", Arial, sans-serif;
  }
  .card {
    position: absolute;
    left: 292px;
    width: 616px;
    height: 352px;
    box-shadow: 0 2px 6px var(--shadow);
    overflow: hidden;
  }
  .card--front { top: 130px; background: var(--paper); }
  .card--back  { top: 506px; height: 350px; background: var(--ink); }

  .brand-faint {
    position: absolute;
    font-weight: 800;
    font-size: 27px;
    letter-spacing: 1px;
    color: var(--faint-mark);
    text-transform: uppercase;
    white-space: nowrap;
  }
  .brand-faint--top    { left: 17px;  top: 17px; }
  .brand-faint--bottom { right: 16px; bottom: 9px; }

  .details-band {
    position: absolute;
    left: 0;
    top: 81px;
    width: 100%;
    height: 207px;
    background: var(--ink);
    color: var(--paper);
    text-align: center;
  }
  .person-name {
    position: absolute;
    left: 0; right: 0;
    top: 44px;
    font-weight: 600;
    font-size: 25px;
  }
  .contact-list {
    position: absolute;
    left: 0; right: 0;
    top: 86px;
    list-style: none;
    font-size: 17px;
    line-height: 26.5px;
  }

  .monogram {
    position: absolute;
    left: 0; right: 0;
    top: 50%;
    transform: translateY(-50%);
    text-align: center;
    color: var(--paper);
    font-weight: 800;
    font-size: 118px;
    line-height: 1;
    letter-spacing: 4px;
  }
</style>
</head>
<body>
  <section class="card card--front" aria-label="Card front">
    <span class="brand-faint brand-faint--top">Marlowe Group</span>
    <div class="details-band">
      <h1 class="person-name">Daniel Marlowe</h1>
      <ul class="contact-list">
        <li>0413586207</li>
        <li>danmarl@inboxmail.test</li>
        <li>www.marlowegroup.test</li>
      </ul>
    </div>
    <span class="brand-faint brand-faint--bottom">Marlowe Group</span>
  </section>

  <section class="card card--back" aria-label="Card back">
    <p class="monogram">M.G</p>
  </section>
</body>
</html>
```